Car rental website design for a UAE car rental company

This project is about creating a new website design for a car rental company located in Dubai (United Arab Emirates), I opened the same project a few months ago but I didn't receive a lot of appealing entries so I closed it but this time I am marking the project as guaranteed to avoid such situation again, if you have already provided a design before then please re-submit again on this project so that it is considered while reviewing all the designs

A few important things:

1- We need a simple non-complex design
2- The final deliverable would be 2 screens (PSD, JPEG ... etc), the first screen is for the home page and the second screen is for an internal page
3- The home page must have a section that end users can use to rent a car online directly from the home page instead of going into some inner pages
4- The current website is very old and not very appealing so avoid creating a similar design (www.crestvane-autos.example)
5- The name is Crestvane but the company rents normal cars (no Limousin cars will be rented) so avoid adding any fancy cars in the images/graphics used in the design, just normal end users cars
6- The expected pages would be: home, About us, Our team, Strategy, Contact us and links to social media pages
7- The attachments include the company's logo and some screens from other car rental companies that provide online rentals/payments

If you have any questions please feel free to ask and please note that we will need the designs urgently

Thanks

Target Market(s)

Dubai - United Arab Emirates

Industry/Entity Type

It Company

Number of Pages Required

2 page

Font styles to use
Sans Serif

Requirements
Must have
• Check the project details
Nice to have
Should not have

```html
<!DOCTYPE html>
<html lang="en">
<head>
<meta charset="utf-8">
<title>Crestvane – Rent a Car</title>
<link rel="stylesheet" href="https://fonts.googleapis.com/css2?family=Arimo:wght@400;700&display=swap">
<style>
:root{
  --crimson:#9b0d3d;
  --crimson-dark:#7a0a2f;
  --title-red:#c8102e;
  --green:#2f7d12;
  --green-light:#4a9e22;
  --ink:#222;
  --line:#d6d6d8;
  --card:#f2f2f4;
  --footer:#8c8c8c;
  --white:#fff;
}
*{box-sizing:border-box;margin:0;padding:0}
html,body{width:1049px;height:1200px;overflow:hidden;background:var(--white)}
body{position:relative;font-family:"Arimo",Arial,sans-serif;color:var(--ink)}
.abs{position:absolute}

.site-header{position:absolute;left:0;top:0;width:1049px;height:72px;background:linear-gradient(#fff,#f3f3f3)}
.brand{left:133px;top:24px;display:flex;align-items:center;gap:8px}
.brand-mark{width:20px;height:20px;background:var(--crimson)}
.brand-name{font-size:22px;font-weight:700;color:var(--crimson)}
.site-search{left:735px;top:19px;width:182px;height:29px;border:1px solid #999;background:#fff;display:flex}
.site-search span{flex:1;font-size:9px;color:#444;padding:9px 0 0 8px}
.site-search button{width:28px;border:0;background:#777;display:flex;align-items:center;justify-content:center}

.main-nav{position:absolute;left:0;top:72px;width:1049px;height:41px;background:linear-gradient(var(--crimson),var(--crimson-dark))}
.main-nav ul{list-style:none;display:flex;margin-left:133px;height:41px}
.main-nav li{color:#fff;font-size:12.5px;display:flex;align-items:center;justify-content:center;border-right:1px solid rgba(0,0,0,.35);box-shadow:1px 0 0 rgba(255,255,255,.12)}
.main-nav li:last-child{border-right:0;box-shadow:none}

.hero{left:0;top:113px;width:1049px;height:444px;background:
 radial-gradient(ellipse at 70% 10%,#f3c77a 0%,#c88a4a 25%,transparent 55%),
 linear-gradient(180deg,#8f7660 0%,#b9905f 35%,#4a3a30 62%,#2b2622 100%)}
.hero-road{left:0;top:380px;width:1049px;height:177px;background:linear-gradient(180deg,rgba(60,55,50,.4),#3a3632)}
.play{left:738px;top:270px}
.slider-dots{left:496px;top:524px;display:flex;gap:3px}
.slider-dots i{width:10px;height:10px;border-radius:50%;background:#fff;display:block}
.slider-dots i.on{background:#555;border:2px solid #fff}

.rental-panel{left:133px;top:113px;width:379px;height:304px;background:#fff;border-radius:0 0 6px 6px;box-shadow:0 3px 8px rgba(0,0,0,.35)}
.rental-panel h2{position:absolute;left:15px;top:24px;display:flex;align-items:center;gap:8px;font-size:20px;font-weight:400;color:var(--title-red)}
.field-label{position:absolute;font-size:11.5px;color:#222}
.field{position:absolute;height:27px;border:1px solid #aaa;background:#fff;font-size:9.5px;color:#555;display:flex;align-items:center;padding:0 6px;justify-content:space-between}
.caret{width:0;height:0;border-left:4px solid transparent;border-right:4px solid transparent;border-top:5px solid #222}
.book-btn{position:absolute;left:259px;top:257px;width:105px;height:29px;border-radius:4px;background:linear-gradient(var(--green-light),var(--green));color:#fff;font-size:11px;font-weight:700;display:flex;align-items:center;justify-content:center}

.call-box{left:213px;top:443px;width:197px;height:55px;background:linear-gradient(#b0134a,var(--crimson-dark));border-radius:3px;display:flex;align-items:center;color:#fff}
.call-box .icon{width:55px;display:flex;justify-content:center;border-right:1px solid rgba(255,255,255,.7);height:32px;align-items:center}
.call-box .txt{padding-left:12px}
.call-box small{display:block;font-size:11px}
.call-box strong{display:block;font-size:20px;font-weight:400}

.welcome{left:0;top:573px;width:1049px;text-align:center}
.welcome h1{font-size:15.5px;font-weight:700;color:var(--crimson)}
.welcome p{font-size:10.5px;line-height:17px;color:#333;margin-top:8px}

.vehicle-card{position:absolute;top:655px;width:252px;height:425px;background:var(--card);box-shadow:0 4px 7px rgba(0,0,0,.18)}
.vehicle-photo{height:168px}
.photo-van{background:linear-gradient(180deg,#9fb4c8 0%,#e8eaec 40%,#c9c9c6 100%)}
.photo-sedan{background:linear-gradient(180deg,#4e5a3f 0%,#8a8f84 45%,#e6e6e4 65%,#3d3d3d 100%)}
.photo-mpv{background:linear-gradient(180deg,#5d8fd0 0%,#a9c9e6 35%,#6b6d72 65%,#d9d3c4 100%)}
.vehicle-card h3{position:absolute;left:13px;top:178px;font-size:15px;color:var(--crimson-dark)}
.price{position:absolute;left:13px;right:20px;top:198px;display:flex;justify-content:space-between;align-items:baseline;font-size:10.5px}
.price b{font-size:12px}
.specs{position:absolute;left:13px;top:230px;border-collapse:collapse;width:225px;font-size:10.5px}
.specs td{height:24px;border-bottom:1px solid var(--line)}
.specs tr:last-child td{border-bottom:0}
.specs td:last-child{font-weight:700;width:48px}
.more-btn{position:absolute;left:85px;top:410px;width:82px;height:26px;border-radius:4px;background:linear-gradient(#444,#0d0d0d);color:#fff;font-size:9.5px;font-weight:700;display:flex;align-items:center;justify-content:center}

.site-footer{left:0;top:1117px;width:1049px;height:83px;background:var(--footer);color:#fff}
.follow{position:absolute;left:134px;top:24px;font-size:9px}
.social{position:absolute;left:134px;top:40px;display:flex;gap:5px}
.social i{display:block;width:20px;height:20px;border-radius:50%}
.footer-links{position:absolute;right:132px;top:20px;font-size:12px}
.copyright{position:absolute;right:132px;top:40px;font-size:9px;font-weight:700}
</style>
</head>
<body>

<header class="site-header">
  <div class="brand abs"><span class="brand-mark"></span><span class="brand-name">Crestvane</span></div>
  <div class="site-search abs"><span>SEARCH</span>
    <button aria-label="Search"><svg width="14" height="14" viewBox="0 0 14 14"><circle cx="5.5" cy="5.5" r="4.3" fill="none" stroke="#fff" stroke-width="1.8"/><line x1="8.6" y1="8.6" x2="13" y2="13" stroke="#fff" stroke-width="2"/></svg></button>
  </div>
</header>

<nav class="main-nav">
  <ul>
    <li style="width:60px">Home</li>
    <li style="width:90px">About us</li>
    <li style="width:92px">Our team</li>
    <li style="width:84px">Vehicles</li>
    <li style="width:86px">Strategy</li>
    <li style="width:110px">My Bookings</li>
    <li style="width:96px">Contact us</li>
  </ul>
</nav>

<section class="hero abs" role="img" aria-label="Family SUV driving on a city road at sunset"></section>
<div class="hero-road abs" aria-hidden="true"></div>
<svg class="play abs" width="70" height="70" viewBox="0 0 70 70" aria-label="Play video"><circle cx="35" cy="35" r="31" fill="rgba(0,0,0,.15)" stroke="#fff" stroke-width="6"/><polygon points="27,21 27,49 50,35" fill="#fff"/></svg>
<div class="slider-dots abs"><i></i><i class="on"></i><i></i><i></i></div>

<form class="rental-panel abs">
  <h2><svg width="16" height="16" viewBox="0 0 16 16"><circle cx="6.5" cy="6.5" r="5" fill="none" stroke="#888" stroke-width="1.4"/><line x1="10" y1="10" x2="15" y2="15" stroke="#888" stroke-width="1.6"/></svg>Search for a car rental</h2>
  <span class="field-label" style="left:15px;top:63px">Location</span>
  <div class="field" style="left:15px;top:79px;width:347px">Enter City or Area</div>

  <span class="field-label" style="left:15px;top:124px">Pickup Date</span>
  <div class="field" style="left:15px;top:140px;width:95px">dd/mm/yy
    <svg width="12" height="12" viewBox="0 0 12 12"><rect x="1" y="2" width="10" height="9" fill="none" stroke="#666"/><path d="M1 5h10M4 5v6M7 5v6M1 8h10" stroke="#666" stroke-width=".7"/></svg></div>
  <div class="field" style="left:114px;top:140px;width:68px">10:00 PM<span class="caret"></span></div>

  <span class="field-label" style="left:194px;top:124px">Drop off Date</span>
  <div class="field" style="left:194px;top:140px;width:95px">dd/mm/yy
    <svg width="12" height="12" viewBox="0 0 12 12"><rect x="1" y="2" width="10" height="9" fill="none" stroke="#666"/><path d="M1 5h10M4 5v6M7 5v6M1 8h10" stroke="#666" stroke-width=".7"/></svg></div>
  <div class="field" style="left:293px;top:140px;width:69px">10:00 PM<span class="caret"></span></div>

  <span class="field-label" style="left:15px;top:182px">Age &amp; Residence</span>
  <div class="field" style="left:15px;top:200px;width:52px">25+<span class="caret"></span></div>
  <span class="field-label" style="left:196px;top:182px">Car&nbsp; Type</span>
  <div class="field" style="left:196px;top:200px;width:117px">Choose car Type<span class="caret"></span></div>

  <div class="book-btn">BOOK NOW</div>
</form>

<div class="call-box abs">
  <div class="icon"><svg width="28" height="20" viewBox="0 0 28 20"><path d="M2 7c0-4 24-4 24 0v3h-6V7c-3-1-9-1-12 0v3H2z" fill="#fff"/><path d="M7 11h14l3 8H4z" fill="#fff"/><circle cx="14" cy="15" r="2.3" fill="#9b0d3d"/></svg></div>
  <div class="txt"><small>CALL US</small><strong>04 555 0273</strong></div>
</div>

<section class="welcome abs">
  <h1>WELCOME TO OUR SITE</h1>
  <p>Crestvane Car Rental is a Dubai fleet renting vans and everyday cars to anyone who needs an extra car for moving, holidays, city trips or whatever it may be.<br>We are unbeatable on service, and most likely on price too. And you can trust that the car you get from us is both clean and tidy!</p>
</section>

<article class="vehicle-card" style="left:133px">
  <div class="vehicle-photo photo-van" role="img" aria-label="White cargo van parked outdoors"></div>
  <h3>Cargo Van</h3>
  <div class="price"><span>Price per day</span><b>AED 150</b></div>
  <table class="specs">
    <tr><td>Car type</td><td>Van</td></tr>
    <tr><td>Max. passengers</td><td>2</td></tr>
    <tr><td>Doors</td><td>5</td></tr>
    <tr><td>Min. driver age</td><td>21</td></tr>
    <tr><td>Gearbox</td><td>Manual</td></tr>
    <tr><td>Air conditioning?</td><td>Yes</td></tr>
    <tr><td>Unlimited km?</td><td>No</td></tr>
  </table>
  <div class="more-btn">READ MORE</div>
</article>

<article class="vehicle-card" style="left:399px">
  <div class="vehicle-photo photo-sedan" role="img" aria-label="White car parked on a driveway"></div>
  <h3>Family Sedan</h3>
  <div class="price"><span>Price per day</span><b>AED 150</b></div>
  <table class="specs">
    <tr><td>Car type</td><td>Sedan</td></tr>
    <tr><td>Max. passengers</td><td>5</td></tr>
    <tr><td>Doors</td><td>4</td></tr>
    <tr><td>Min. driver age</td><td>21</td></tr>
    <tr><td>Gearbox</td><td>Auto</td></tr>
    <tr><td>Air conditioning?</td><td>Yes</td></tr>
    <tr><td>Unlimited km?</td><td>No</td></tr>
  </table>
  <div class="more-btn">READ MORE</div>
</article>

<article class="vehicle-card" style="left:664px">
  <div class="vehicle-photo photo-mpv" role="img" aria-label="Grey people carrier on a beach road"></div>
  <h3>Family MPV</h3>
  <div class="price"><span>Price per day</span><b>AED 150</b></div>
  <table class="specs">
    <tr><td>Car type</td><td>MPV</td></tr>
    <tr><td>Max. passengers</td><td>7</td></tr>
    <tr><td>Doors</td><td>5</td></tr>
    <tr><td>Min. driver age</td><td>21</td></tr>
    <tr><td>Gearbox</td><td>Auto</td></tr>
    <tr><td>Air conditioning?</td><td>Yes</td></tr>
    <tr><td>Unlimited km?</td><td>No</td></tr>
  </table>
  <div class="more-btn">READ MORE</div>
</article>

<footer class="site-footer abs">
  <span class="follow">FOLLOW US ON</span>
  <div class="social"><i style="background:#3b5a9a"></i><i style="background:#3fa9dc"></i><i style="background:#e8742a"></i></div>
  <div class="footer-links">Home &nbsp;| &nbsp;About us &nbsp;| &nbsp;Our team &nbsp;| &nbsp;Vehicles &nbsp;| &nbsp;Strategy &nbsp;| &nbsp;My Bookings &nbsp;| &nbsp;Contact us</div>
  <div class="copyright">COPYRIGHTS @ 2014 ALL RIGHTS RESERVED</div>
</footer>

</body>
</html>
```